Request for Business Card Design

Hi. My name is Marlene, I am looking for a new business card design for my company, Quarrow Signal Instruments, LLC. I really like the design you did for Tarsel Venture and was hoping you could do something similar using our full logo and our mark. I am also open to any raised texture design using our mark. I have attached our full logo, which would need to be somewhere on the card, as well as the mark in both outline and full form, as well as our brand colors / guide. The card does not have to be white, as long as our logo and mark appear. I actually like darker colored business cards more, but am open to all options. If you are interested in working with me, please let me know. We would also take the business card design into letterhead design if you can do that.

```html
<!DOCTYPE html>
<html lang="en">
<head>
<meta charset="utf-8">
<title>Quarrow Signal Instruments – Business Card</title>
<link rel="stylesheet" href="https://fonts.googleapis.com/css2?family=Open+Sans:wght@400;600;700&display=swap">
<style>
  :root {
    --stage: #222222;
    --card-back: #2f2f30;
    --card-front: #3c3c3e;
    --accent: #1d9fcf;
    --text-light: #f4f6f7;
    --deco: #46525a;
    --emboss: #2a2a2b;
  }
  * { margin: 0; padding: 0; box-sizing: border-box; }
  html, body {
    width: 1200px; height: 780px; overflow: hidden;
    background: var(--stage);
    font-family: "Open Sans", Arial, sans-serif;
  }
  .stage { position: relative; width: 1200px; height: 780px; }
  .card {
    position: absolute; width: 540px; height: 309px;
    border-radius: 3px; overflow: hidden;
  }

  /* Back side */
  .card--back { left: 60px; top: 70px; background: var(--card-back); }
  .back__pattern {
    position: absolute; inset: 0;
    background: linear-gradient(200deg, #6a6a6c 0%, #3d3d3f 35%, #2c2c2d 70%);
  }
  .back__brand {
    position: absolute; right: 34px; bottom: 40px;
    display: flex; align-items: center; gap: 8px;
    color: var(--accent); font-weight: 700; font-size: 12px;
    letter-spacing: 0.06em; text-transform: uppercase;
  }
  .back__brand-dot { width: 12px; height: 12px; border-radius: 50%; background: var(--accent); }

  /* Front side */
  .card--front { left: 600px; top: 400px; background: var(--card-front); }
  .front__deco {
    position: absolute; right: -60px; top: 20px;
    width: 360px; height: 360px; border-radius: 50%;
    background: radial-gradient(circle, rgba(70,82,90,0.0) 40%, rgba(70,82,90,0.85) 41%, rgba(70,82,90,0.85) 60%, rgba(70,82,90,0) 61%);
  }
  .front__brand {
    position: absolute; left: 26px; bottom: 28px;
    writing-mode: vertical-rl; transform: rotate(180deg);
    color: var(--emboss); font-weight: 700; font-size: 30px;
    letter-spacing: 0.04em; text-transform: uppercase; line-height: 1;
  }
  .front__bar {
    position: absolute; right: 0; top: 40px;
    width: 22px; height: 40px; background: var(--accent);
  }
  .front__info {
    position: absolute; right: 34px; top: 38px;
    text-align: right; color: var(--text-light);
  }
  .front__name { color: var(--accent); font-weight: 700; font-size: 32px; line-height: 1; }
  .front__role { font-weight: 600; font-size: 14px; margin-top: 2px; }
  .front__address { font-size: 13px; line-height: 1.35; margin-top: 18px; }
  .front__contacts { list-style: none; font-size: 13px; line-height: 1.4; margin-top: 12px; }
  .front__contacts li { display: flex; justify-content: flex-end; align-items: center; gap: 8px; }
  .icon { width: 12px; height: 12px; fill: none; stroke: var(--accent); stroke-width: 1.6; }
</style>
</head>
<body>
<main class="stage">

  <section class="card card--back" aria-label="Card back">
    <div class="back__pattern" role="img" aria-label="Repeating brand mark texture fading from light to dark"></div>
    <div class="back__brand"><span class="back__brand-dot"></span>Quarrow Signal Instruments</div>
  </section>

  <section class="card card--front" aria-label="Card front">
    <div class="front__deco" role="img" aria-label="Large faint brand mark decoration"></div>
    <div class="front__brand">Quarrow</div>
    <div class="front__bar"></div>
    <div class="front__info">
      <p class="front__name">Marlene</p>
      <p class="front__role">Director</p>
      <p class="front__address">1180 Ferrow Park Road •<br>Aldenbrook, CO 80612</p>
      <ul class="front__contacts">
        <li>+001 555 210 4837
          <svg class="icon" viewBox="0 0 12 12"><path d="M3 1 L5 3 L4 5 Q5 7 7 8 L9 7 L11 9 L9 11 Q3 10 1 3 Z"/></svg></li>
        <li>+001 555 210 4839
          <svg class="icon" viewBox="0 0 12 12"><rect x="1" y="4" width="10" height="7"/><rect x="3" y="1" width="6" height="3"/></svg></li>
        <li>www.quarrowsignal.com
          <svg class="icon" viewBox="0 0 12 12"><circle cx="6" cy="6" r="5"/><path d="M1 6 H11 M6 1 Q3 6 6 11 Q9 6 6 1"/></svg></li>
        <li>info@quarrowsignal.com
          <svg class="icon" viewBox="0 0 12 12"><rect x="1" y="2.5" width="10" height="7"/><path d="M1 2.5 L6 7 L11 2.5"/></svg></li>
      </ul>
    </div>
  </section>

</main>
</body>
</html>
```